Business Card Design - Amberfield Court

We are looking at a new design for our business cards that has a modern and professional look. We run a residential aged care facility focussing on the care of residents. The cards will be used for potential clients, consultants and business opportunities in this sector. Blue and white is our main colours and would to see these colours incorporated in the design.
Industry/Entity Type
Business
Contact Information for Business Card
Amberfield Court, Darren Walsh, dwalsh@amberfieldcourt.com.au, Finance Manager, 0472 639 208, BCom, 37 Marrabel Crescent, Brindle Vale, Qld 4093.
Look and feel
Each slider illustrates characteristics of the customer's brand and the style your logo design should communicate.

```html
<!DOCTYPE html>
<html lang="en">
<head>
<meta charset="utf-8">
<title>Amberfield Court – Business Card</title>
<link rel="stylesheet" href="https://fonts.googleapis.com/css2?family=Arimo:wght@400;700&display=swap">
<style>
  :root {
    --canvas: #e9e6e1;
    --card-white: #ffffff;
    --card-shade: #ececec;
    --brand-blue: #4a7a94;
    --brand-blue-dark: #3e6a82;
    --text-on-blue: #ffffff;
    --text-dark: #3f4a52;
    --shadow: rgba(0, 0, 0, 0.22);
  }
  * { box-sizing: border-box; margin: 0; padding: 0; }
  html, body {
    width: 1200px;
    height: 950px;
    overflow: hidden;
    background: var(--canvas);
    font-family: "Arimo", Arial, sans-serif;
  }
  .sheet {
    width: 1200px;
    height: 950px;
    display: flex;
    flex-direction: column;
    align-items: center;
    justify-content: center;
    gap: 34px;
  }
  .card {
    width: 700px;
    height: 424px;
    box-shadow: 0 10px 26px var(--shadow);
    position: relative;
    overflow: hidden;
  }

  /* Front: contact panel + brand panel */
  .card--front { display: flex; background: var(--card-white); }
  .contact-panel {
    width: 400px;
    height: 100%;
    background: var(--brand-blue);
    color: var(--text-on-blue);
    padding: 44px 30px 0 52px;
    display: flex;
    flex-direction: column;
  }
  .contact-panel .name {
    font-size: 27px;
    font-weight: 700;
    letter-spacing: 0.2px;
  }
  .contact-panel .name .credential { font-size: 22px; }
  .contact-panel .role {
    font-size: 20px;
    margin-top: 4px;
  }
  .address {
    margin-top: 88px;
    font-size: 18px;
    line-height: 1.35;
  }
  .contact-list {
    list-style: none;
    font-size: 18px;
    line-height: 1.35;
  }
  .contact-list li {
    display: flex;
    align-items: center;
    gap: 9px;
    margin-left: -26px;
  }
  .contact-list svg { width: 17px; height: 17px; flex: none; }

  .brand-panel {
    flex: 1;
    background: linear-gradient(160deg, var(--card-white) 0%, var(--card-shade) 100%);
    display: flex;
    align-items: center;
    justify-content: center;
  }
  .brand-lockup {
    display: flex;
    align-items: center;
    gap: 12px;
  }
  .brand-mark {
    width: 26px;
    height: 26px;
    border-radius: 50%;
    background: var(--brand-blue);
    flex: none;
  }
  .brand-name {
    font-size: 26px;
    color: var(--brand-blue-dark);
    letter-spacing: 2px;
    text-transform: uppercase;
  }

  /* Back: brand + web address */
  .card--back {
    background: linear-gradient(200deg, var(--card-white) 0%, var(--card-shade) 100%);
    display: flex;
    flex-direction: column;
    align-items: center;
    justify-content: center;
    gap: 18px;
  }
  .card--back .brand-name { font-size: 34px; }
  .card--back .brand-mark { width: 32px; height: 32px; }
  .web-address {
    font-size: 22px;
    color: var(--text-dark);
    letter-spacing: 0.5px;
  }
</style>
</head>
<body>
<main class="sheet">
  <section class="card card--front" aria-label="Business card front">
    <div class="contact-panel">
      <p class="name">Darren Walsh <span class="credential">BCom</span></p>
      <p class="role">Finance Manager</p>
      <p class="address">37 Marrabel Crescent<br>Brindle Vale, Qld 4093.</p>
      <ul class="contact-list">
        <li>
          <svg viewBox="0 0 20 20" aria-hidden="true"><path fill="#fff" d="M4 6c0-2 3-3 6-3s6 1 6 3v2h-3V6.5C12 6 8 6 7 6.5V8H4zM5 9h10l2 7H3z"/><circle cx="10" cy="12.5" r="2" fill="#4a7a94"/></svg>
          <span>0472 639 208</span>
        </li>
        <li>
          <svg viewBox="0 0 20 20" aria-hidden="true"><rect x="2" y="5" width="16" height="11" rx="1" fill="#fff"/><path d="M2.5 5.5 10 11l7.5-5.5" fill="none" stroke="#4a7a94" stroke-width="1.4"/></svg>
          <span>dwalsh@amberfieldcourt.com.au</span>
        </li>
        <li>
          <svg viewBox="0 0 20 20" aria-hidden="true"><circle cx="10" cy="10" r="8" fill="#fff"/><ellipse cx="10" cy="10" rx="3.2" ry="8" fill="none" stroke="#4a7a94" stroke-width="1.2"/><path d="M2 10h16" stroke="#4a7a94" stroke-width="1.2"/></svg>
          <span>www.amberfieldcourt.com.au</span>
        </li>
      </ul>
    </div>
    <div class="brand-panel">
      <div class="brand-lockup">
        <span class="brand-mark" aria-hidden="true"></span>
        <span class="brand-name">Amberfield Court</span>
      </div>
    </div>
  </section>

  <section class="card card--back" aria-label="Business card back">
    <div class="brand-lockup">
      <span class="brand-mark" aria-hidden="true"></span>
      <span class="brand-name">Amberfield Court</span>
    </div>
    <p class="web-address">amberfieldcourt.com.au</p>
  </section>
</main>
</body>
</html>
```